Step Forth Daily newsletter - Mail Chimp

Step Forth Daily - Empowering Life Coach needs Mail Chimp Newsletter Template. This is a newsletter I will send out monthly to current clients and prospective clients to offer (hopefully) inspiring and uplifting content AND to give info and dates of my upcoming workshops and retreats.

I have attached a word document with all of the different sections of the mail chimp template I would like to have - and hte actual content for the first newsletter.

I'd like to look uplifting, fun, inspiring.

I also need it to be easy for me to use to update in the future :)

Target Market(s)

Women - moms

Industry/Entity Type

Life Coaching

Requirements
Nice to have
• Color theme to match my "Step Forth Daily" logo

```html
<!DOCTYPE html>
<html lang="en">
<head>
<meta charset="utf-8">
<title>Step Forth Daily – Monthly Newsletter</title>
<link href="https://fonts.googleapis.com/css2?family=Lato:wght@400;700&family=Playfair+Display:ital,wght@0,400;1,400&display=swap" rel="stylesheet">
<style>
:root{
  --purple:#5b1f7c;
  --orange:#f7941d;
  --orange-deep:#f26a1b;
  --blue:#2e9fd9;
  --green:#7cc242;
  --ink:#3c3c3c;
  --white:#ffffff;
  --light-grey:#d9d9d9;
}
*{margin:0;padding:0;box-sizing:border-box}
html,body{width:1200px;height:5217px;overflow:hidden;background:var(--white)}
body{font-family:"Lato",sans-serif;color:var(--ink);font-size:22px;line-height:1.7;position:relative}
section,header,footer{position:absolute;left:0;width:1200px}
.serif{font-family:"Playfair Display",serif}

/* header */
.site-header{top:0;height:170px;background:var(--white);z-index:2}
.brand{position:absolute;left:64px;top:52px;display:flex;align-items:center;gap:14px;font-family:"Lato",sans-serif;font-weight:700;font-size:40px;color:var(--purple)}
.brand-dot{width:30px;height:30px;border-radius:50%;background:var(--orange)}
.follow{position:absolute;right:40px;top:50px;display:flex;align-items:center;gap:18px;font-weight:700;color:var(--purple);font-size:22px}
.follow span.icon{width:30px;height:30px;border-radius:50%;background:var(--green)}
.hero{top:120px;height:480px;background:linear-gradient(180deg,#f9d77e 0%,#f6a844 55%,#c9701f 100%)}
.hero-wave{position:absolute;top:-2px;left:0}

/* intro */
.intro{top:600px;height:705px}
.intro-photo{position:absolute;left:22px;top:62px;width:285px;height:380px;background:linear-gradient(135deg,#f2c23a,#e58a2b 60%,#6e7fa8)}
.intro-text{position:absolute;left:335px;top:50px;width:840px;font-size:23px;line-height:1.72}
.intro-text h2{font-style:italic;font-weight:400;color:var(--orange-deep);font-size:36px;line-height:1.3;margin-bottom:14px}
.sign{font-weight:700;margin-top:14px}
.sign-name{font-family:"Playfair Display",serif;font-style:italic;color:var(--blue);font-size:38px;line-height:1.1}

/* tips */
.tips{top:1305px;height:1445px;background:var(--purple);color:var(--white)}
.stripe{position:absolute;height:24px;background:var(--orange)}
.tips-inner{position:absolute;left:18px;top:80px;width:1160px;font-size:21.5px;line-height:1.7}
.tips h2{font-family:"Playfair Display",serif;font-weight:400;font-size:44px;margin-bottom:22px}
.tips h3{font-family:"Playfair Display",serif;font-style:italic;font-weight:400;color:var(--orange);font-size:36px;line-height:1.4;margin:30px 0 14px}
.tips h3.first{margin-top:0}
.tips p{margin-bottom:18px}
.ticks{list-style:none;margin:6px 0 14px}
.ticks li{display:flex;align-items:center;gap:18px;margin-bottom:10px}

/* quotes */
.quotes{top:2750px;height:675px}
.quote-card{position:absolute;top:137px;height:443px;display:flex;flex-direction:column;justify-content:center;align-items:center;text-align:center;overflow:hidden}
.quote-a{left:236px;width:290px;background:linear-gradient(180deg,#8a6a3f,#3d4b36);color:var(--white);font-weight:700;font-size:31px;line-height:1.12;padding:24px;text-transform:uppercase}
.quote-b{left:532px;width:436px;background:linear-gradient(180deg,#d6e2ee,#9fb3c5);color:#2b2b2b;font-family:"Playfair Display",serif;font-size:19px;line-height:1.45;padding:20px}
.quote-b .q-title{color:#a0153e;font-size:32px;line-height:1.2;margin-bottom:14px}
.quote-b .q-em{color:#a0153e;font-style:italic;font-size:24px}
.quote-b .q-by{font-style:italic;font-size:15px;margin-top:10px}

/* books */
.books{top:3425px;height:455px;background:var(--blue);color:var(--white)}
.book-art{position:absolute;left:100px;top:45px;width:260px;height:300px;background:linear-gradient(135deg,#e8e8e8,#9a9a9a)}
.books-text{position:absolute;left:487px;top:102px;width:680px;font-size:22px;line-height:1.7}
.books-text h2{font-family:"Playfair Display",serif;font-weight:400;font-size:40px;margin-bottom:14px}

/* events */
.events{top:3880px;height:780px}
.events-box{position:absolute;left:132px;top:70px;width:1052px;height:613px;border:3px solid var(--light-grey)}
.events-side{position:absolute;left:0;top:0;width:303px;height:100%;background:var(--green);color:var(--white);text-align:center;font-weight:700;font-size:22px;line-height:1.5;padding:40px 12px}
.side-brand{display:flex;flex-direction:column;align-items:center;gap:10px;font-size:26px;letter-spacing:1px;margin-bottom:60px}
.side-brand .dot{width:36px;height:36px;border-radius:50%;background:var(--white)}
.side-label{color:#2d4e12;margin:10px 0 6px}
.events-main{position:absolute;left:340px;top:28px;width:690px;font-size:21.5px;line-height:1.65}
.events-main h2{font-family:"Playfair Display",serif;font-weight:400;color:var(--orange-deep);font-size:40px;margin-bottom:16px}
.events-main p{margin-bottom:18px}

/* closing */
.closing{top:4660px;height:450px;background:var(--blue);color:var(--white)}
.closing-text{position:absolute;left:80px;top:100px;font-family:"Playfair Display",serif;font-size:38px;line-height:1.42}
.closing-card{position:absolute;left:762px;top:62px;width:360px;height:320px;border:5px solid var(--white);background:linear-gradient(135deg,#3a3a3a,#7d6b4f);display:flex;align-items:center;justify-content:flex-end}
.closing-quote{width:200px;margin-right:14px;background:#f4ecd0;color:#222;font-size:13px;line-height:1.35;padding:10px;font-style:italic}
.closing-by{position:absolute;left:14px;bottom:10px;color:#f4ecd0;font-size:26px}

.site-footer{top:5110px;height:107px;text-align:center;font-size:16px;padding-top:42px;color:#555}
</style>
</head>
<body>

<header class="site-header">
  <div class="brand"><span class="brand-dot"></span>Step Forth Daily</div>
  <div class="follow">Follow Us: <span class="icon"></span><span class="icon"></span><span class="icon"></span><span class="icon"></span></div>
</header>
<section class="hero" role="img" aria-label="Sunset photo of two hands forming a heart shape against the sun">
  <svg class="hero-wave" width="1200" height="90" viewBox="0 0 1200 90"><path d="M0 0H1200V40C900 95 500 90 0 60Z" fill="#fff"/></svg>
</section>

<section class="intro">
  <div class="intro-photo" role="img" aria-label="Portrait photo of the coach by a pool"></div>
  <div class="intro-text">
    <h2>Hello Friends!!</h2>
    <p>I am excited to (hopefully) add a little love to your in-box with this newsletter. I love connecting with moms and helping them find tools to make their lives happier, more intentional, and more fun and this is a new way to do that! If you don't know me well, I am a certified Open Horizons Trainer and I lead coaching groups for moms. My Open Horizons workshops and Empowered Moms Coaching Group have the goal of fostering connections between amazing women and empowering moms with tools to build lives they are enthusiastic about living, on purpose – and that will be the goal of this newsletter, as well! I hope you find something useful and helpful and enjoy receiving this info (and if not, feel free to unsubscribe and my feelings will not be hurt!</p>
    <p class="sign">With love,</p>
    <p class="sign-name">Dana</p>
  </div>
</section>

<section class="tips">
  <div class="stripe" style="right:0;top:-12px;width:420px;transform:skewY(-2deg)"></div>
  <div class="tips-inner">
    <h2>Step Forth Daily Tips &amp; Tools:</h2>
    <h3 class="first">Building Happiness</h3>
    <p>I firmly believe that thinking about your happiness is important and that happiness itself is a worthwhile goal! If you think about all the things you focus on in your life and all the goals you set for yourself, all of those things are leading you toward feeling happier. Happiness, in the end, is the ultimate goal.</p>
    <p>Of course, what makes each person happy is totally different – and that's awesome and one part of what makes life fun and exciting! Many happiness experts and authors note that the key ingredieents in our lives that will make us happier are pursuing 2 categories:</p>
    <ul class="ticks">
      <li><svg width="22" height="18" viewBox="0 0 22 18"><path d="M2 9l6 6L20 2" stroke="#fff" stroke-width="4" fill="none"/></svg>Things that bring us pleasure (positive emotions) and</li>
      <li><svg width="22" height="18" viewBox="0 0 22 18"><path d="M2 9l6 6L20 2" stroke="#fff" stroke-width="4" fill="none"/></svg>Things that bring us meaning &amp; fulfillment</li>
    </ul>
    <p>Give yourself a minute to think about (it's extra powerful if you write it down!) what makes YOU happy.</p>
    <h3>What are things that make you feel happy / provide you with pleasure (little and big things!)?</h3>
    <p>For me: joking &amp; laughing with my kids &amp; husband, petting with my dog, sitting with a soft blanket and a book, my first sip of coffee in the morning, walking in nature, travelling, scuba diving, exercise classes, making my friends laugh.</p>
    <h3>What are things that are meaningful to you / make you feel fulfilled (little and big things!)?</h3>
    <p>For me: teaching Open Horizons workshops, spending quality time with my family, making gratitude lists, volunteering, leading moms' coaching groups, making my kids breakfast.</p>
    <h3>How could you add more of those things that bring you happiness to your days?</h3>
    <p>Try to add 1 or 2 of those things per week and see how your happiness increases! You are worth it!</p>
  </div>
  <div class="stripe" style="left:0;bottom:-12px;width:460px;transform:skewY(-2deg)"></div>
</section>

<section class="quotes">
  <div class="quote-card quote-a" role="img" aria-label="Quote card over a photo of a woman in a field">Happiness is not something you postpone for the future; it is something you design for the present.</div>
  <div class="quote-card quote-b" role="img" aria-label="Quote card over a soft sky photo">
    <div class="q-title">Happiness is found<br>in the simplest of things.</div>
    <div>Happiness is found in gratitude,<br>in a kept promise,<br>in a good conversation,<br>in love,<br>in friendship,<br>in an achieved goal,<br>in a fond memory;</div>
    <div class="q-em">in all the simple magnificence of life</div>
    <div class="q-by">– Dr. Alan Pierce</div>
  </div>
</section>

<section class="books">
  <div class="stripe" style="left:0;top:-12px;width:420px;transform:skewY(-2deg)"></div>
  <div class="book-art" role="img" aria-label="Placeholder book cover shown as a tilted 3D book"></div>
  <div class="books-text">
    <h2>Empowering Books</h2>
    <p>I love to read uplifting, inspiring material. Each newsletter, I'll suggest a few books that I've enjoyed!<br>The Joy Ledger by Marla Quinn<br>Bold Little Steps: How to Quiet Your Doubts and Start Living a Brighter Life" by Tessa Lowell</p>
  </div>
  <div class="stripe" style="right:0;bottom:-12px;width:480px;transform:skewY(-2deg)"></div>
</section>

<section class="events">
  <div class="events-box">
    <div class="events-side">
      <div class="side-brand"><span class="dot"></span>OPEN HORIZONS</div>
      <div class="side-label">Dates:</div>
      <div>3 morning workshop<br>September 27, October 4, October 11<br>9:30 – 12:30<br>Dana's home in Cedar Ridge</div>
      <div class="side-label">Interested?</div>
      <div>Email Me:<br>hello@stepforthdaily.com</div>
    </div>
    <div class="events-main">
      <h2>Upcoming Events</h2>
      <p>I lead an Open Horizons Workshop 2-3 times per year. The next one is coming up in September/October.<br>More details to come – but here is a little info…</p>
      <p>Moms - Back to School, Back to You!<br>In September, the kids will be going back to school and you can spend time focusing on YOU. Let this be the year where you take time to focus on yourself so that you can feel amazing, focused, fulfilled, purposeful, and happier! Take the time to learn some simple tools to help you live a life you love, deliberately, instead of just juggling what comes at you and juggling your to-do list. In this workshop, you will be empowered to build a life you love.</p>
    </div>
  </div>
</section>

<section class="closing">
  <div class="stripe" style="right:0;top:-12px;width:480px;transform:skewY(-2deg)"></div>
  <div class="closing-text">Enjoy the rest of Summer Break!<br>Savor each amazing day!<br>How can you add a little more<br>HAPPY to your August??<br>Make the choice and do it!</div>
  <div class="closing-card" role="img" aria-label="Quote card over a portrait photo">
    <div class="closing-quote">"When I was 5 years old, my mother always told me that happiness was the key to life. When I went to school, they asked me what I wanted to be when I grew up. I wrote down 'happy'. They told me I didn't understand the assignment, and I told them they didn't understand life."</div>
    <div class="closing-by serif">- Rowan Ellis</div>
  </div>
  <div class="stripe" style="left:0;bottom:-12px;width:420px;transform:skewY(-2deg)"></div>
</section>

<footer class="site-footer">Copyright © 2018 Company Name All Right Reserved</footer>

</body>
</html>
```